Venture 482 - Lumora Book Cover

I am looking for a Lumora book cover for my book about "Venture 482".
The Book is Titled:
Venture 482 Ascended
Shaping Outcomes: Paths To Unlocking Cosmic Truths
Author is Dorian Pell
Here is a book description that may help you understand more about it:
Inspired by the genius of Edwin Marlowe, this comprehensive guide delves into the ancient wisdom and cutting-edge science behind the 482 method, a powerful tool for manifesting your desires. Whether you're seeking personal growth, financial success, or spiritual enlightenment, this book provides advanced techniques and methods to transform your dreams into reality.
Any questions please ask.
Thanks
Owen

```html
<!DOCTYPE html>
<html lang="en">
<head>
<meta charset="utf-8">
<title>Venture 482 Ascended — Dorian Pell</title>
<link rel="stylesheet" href="https://fonts.googleapis.com/css2?family=Cinzel:wght@400;600;700;800&family=Raleway:wght@300&family=Tinos&display=swap">
<style>
  :root {
    --sky-top: #24364f;
    --sky-mid: #5f82a8;
    --sky-low: #a9c0d6;
    --horizon: #e9eef1;
    --ground: #9a999b;
    --ground-dark: #6e6e72;
    --title-cream: #f7e6d8;
    --subtitle-cream: #fbf7dd;
    --caption-white: #ffffff;
    --shadow-dark: rgba(20, 20, 30, 0.85);
  }
  html, body {
    margin: 0;
    padding: 0;
    overflow: hidden;
    background: #ffffff;
  }
  .cover {
    position: relative;
    width: 805px;
    height: 1200px;
    overflow: hidden;
  }
  .cover-scene {
    position: absolute;
    inset: 0;
    background: linear-gradient(
      to bottom,
      var(--sky-top) 0%,
      var(--sky-mid) 28%,
      var(--sky-low) 52%,
      var(--horizon) 64%,
      var(--ground) 68%,
      var(--ground-dark) 100%
    );
  }
  .line {
    position: absolute;
    left: 0;
    width: 805px;
    margin: 0;
    text-align: center;
    white-space: nowrap;
  }
  .author {
    top: 72px;
    padding-left: 40px;
    box-sizing: border-box;
    font-family: "Cinzel", serif;
    font-weight: 400;
    font-size: 46px;
    letter-spacing: 0.34em;
    color: var(--title-cream);
  }
  .title-word {
    top: 178px;
    padding-left: 32px;
    box-sizing: border-box;
    font-family: "Cinzel", serif;
    font-weight: 800;
    font-size: 92px;
    line-height: 1;
    color: var(--title-cream);
    text-shadow: 3px 4px 6px rgba(30, 40, 60, 0.35);
  }
  .title-number {
    top: 262px;
    padding-left: 36px;
    box-sizing: border-box;
    font-family: "Cinzel", serif;
    font-weight: 700;
    font-size: 286px;
    line-height: 1;
    letter-spacing: -0.02em;
    color: var(--title-cream);
  }
  .edition {
    top: 528px;
    padding-left: 44px;
    box-sizing: border-box;
    font-family: "Cinzel", serif;
    font-weight: 700;
    font-size: 58px;
    line-height: 1;
    letter-spacing: 0.28em;
    color: var(--subtitle-cream);
    text-shadow: 3px 3px 0 var(--shadow-dark);
  }
  .subtitle-lead {
    top: 1030px;
    font-family: "Raleway", sans-serif;
    font-weight: 300;
    font-size: 32px;
    letter-spacing: 0.04em;
    color: var(--caption-white);
  }
  .subtitle-rest {
    top: 1084px;
    font-family: "Tinos", serif;
    font-size: 27px;
    line-height: 36px;
    color: var(--caption-white);
  }
</style>
</head>
<body>
  <main class="cover">
    <div class="cover-scene" role="img" aria-label="Surreal landscape: a man in a dark suit standing before a tall mirrored doorway under a blue cloudy sky, with a reflecting mirror pathway across a pale ground"></div>
    <p class="line author">DORIAN PELL</p>
    <h1 class="line title-word">VENTURE</h1>
    <p class="line title-number">482</p>
    <p class="line edition">ASCENDED</p>
    <p class="line subtitle-lead">SHAPING OUTCOMES:</p>
    <p class="line subtitle-rest">Paths to unlocking<br>cosmic truths</p>
  </main>
</body>
</html>
```